Business Card: RW Office Partners - Your organised problem solver

Business Name: RW Office Partners
Website: www.rwofficepartners.com.au
Email: marisol@rwofficepartners.com.au
Mobile: 61 482 907 236
Facebook: @rwofficepartners
Instrgram: @rwofficepartners

Brading Colours:
HEX
#986474
#ddccd3
#7a8498
#c9d8e4
#000000
#ffffff

Tag Line: Sorted tasks, steady growth

Link to DRAFT website:
https://deskhelpcollective.wixsite.com/rw-office-partners

About Page from the website:
My name is Marisol Wrenfield, and I would love to assist you to become more productive in your day to day and achieve your business and personal goals.
My mission is to give you time, time to work on the important tasks of your business or to be able to spend more time with your family. I will take on the tasks you don’t have time for, don’t know well or simply don’t like to do.
I have an extensive background in Administration, Tender Coordination, Document Control, WHS and Quality Management working primarily in the Construction, Mining and Corporate World.
I am passionate about being organised, having order and making things in your life (and mine) easier! I love to watch something unfold and grow into something amazing! I am known for being the go-to problem solver, the organiser of all things, producing high standards of work even under pressure. I’m also a confident communicator, and I understand that you’re busy running your business.

Target Market(s)

Small to Medium Business who require assistance in their business by a virtual assistant.

Industry/Entity Type

Virtual Assistant

Contact Information for Business Card

Mobile: 61 482 907 236

Font styles to use
Sans Serif

Colors
ffffff

Requirements
Must have
• Branding Colours as outlined.
Contact Details as outlined.
Logo as provided.
Proper contact details - mobile, facebook, instragm, website.
Simple, Elegant, very clean looking.
Should not have
• Note cute with pictures.
Not too girly as still want to market to construction companies.

```html
<!DOCTYPE html>
<html lang="en">
<head>
<meta charset="utf-8">
<title>RW Office Partners – Business Card</title>
<link rel="stylesheet" href="https://fonts.googleapis.com/css2?family=Montserrat:wght@500;600&family=Roboto:wght@400;700&display=swap">
<style>
  :root {
    --mauve: #986474;
    --blush: #ddccd3;
    --slate: #7a8498;
    --mist: #c9d8e4;
    --ink: #000000;
    --paper: #ffffff;
    --card: #1d1b1f;
    --backdrop: #3a3a3c;
    --faint: #3a363c;
  }
  * { box-sizing: border-box; margin: 0; padding: 0; }
  html, body { width: 799px; height: 1200px; overflow: hidden; }
  body {
    background: var(--backdrop);
    font-family: "Roboto", Arial, sans-serif;
    position: relative;
  }
  .card {
    position: absolute;
    left: 60px;
    width: 680px;
    height: 415px;
    background: var(--card);
    border-radius: 4px;
    box-shadow: 0 14px 30px rgba(0,0,0,.45);
  }
  .card--front { top: 130px; }
  .card--back { top: 655px; }

  .brand-name {
    font-family: "Montserrat", Arial, sans-serif;
    font-weight: 600;
    color: var(--mauve);
    letter-spacing: .5px;
    white-space: nowrap;
  }
  .card--front .brand-name {
    position: absolute;
    left: 0; right: 0;
    top: 150px;
    text-align: center;
    font-size: 46px;
  }
  .socials { list-style: none; color: var(--paper); font-size: 17px; }
  .socials li { display: flex; align-items: center; gap: 8px; }
  .social-mark {
    width: 14px; height: 14px;
    background: var(--mauve);
    border-radius: 3px;
    flex: none;
  }
  .card--front .socials {
    position: absolute;
    left: 90px; top: 300px;
    display: flex; gap: 22px;
  }

  .card--back .brand-block {
    position: absolute;
    right: 40px; top: 56px;
    text-align: right;
  }
  .card--back .brand-name { font-size: 34px; }
  .tagline {
    margin-top: 6px;
    font-family: "Montserrat", Arial, sans-serif;
    font-weight: 500;
    font-size: 13px;
    letter-spacing: 3px;
    text-transform: uppercase;
    color: var(--faint);
  }
  .person { position: absolute; left: 40px; top: 150px; }
  .person-name {
    font-weight: 700;
    font-size: 22px;
    color: var(--mauve);
  }
  .person-role { color: var(--paper); font-size: 15px; margin-top: 4px; }
  .divider {
    position: absolute;
    left: 300px; right: 40px; top: 205px;
    height: 1px;
    background: var(--slate);
  }
  .contacts {
    list-style: none;
    position: absolute;
    left: 40px; top: 226px;
    color: var(--paper);
    font-size: 15px;
    line-height: 26px;
  }
  .contacts li { display: flex; align-items: center; gap: 10px; }
  .contacts svg { width: 13px; height: 13px; fill: var(--mauve); flex: none; }
  .card--back .socials {
    position: absolute;
    right: 40px; top: 318px;
    line-height: 28px;
  }
</style>
</head>
<body>
  <section class="card card--front">
    <div class="brand-name">RW Office Partners</div>
    <ul class="socials">
      <li><span class="social-mark"></span>@rwofficepartners</li>
      <li><span class="social-mark"></span>@rwofficepartners</li>
    </ul>
  </section>

  <section class="card card--back">
    <div class="brand-block">
      <div class="brand-name">RW Office Partners</div>
      <div class="tagline">Sorted tasks, steady growth</div>
    </div>
    <div class="person">
      <div class="person-name">Marisol Wrenfield</div>
      <div class="person-role">Virtual Assistant</div>
    </div>
    <div class="divider"></div>
    <ul class="contacts">
      <li><svg viewBox="0 0 16 16"><path d="M3 1h3l1.5 4-2 1.5a9 9 0 0 0 4 4L11 8.5l4 1.5v3a2 2 0 0 1-2 2A12 12 0 0 1 1 3a2 2 0 0 1 2-2z"/></svg>61 482 907 236</li>
      <li><svg viewBox="0 0 16 16"><path d="M1 3h14v10H1z M1 3l7 6 7-6" stroke="#1d1b1f" stroke-width="1"/></svg>marisol@rwofficepartners.com.au</li>
      <li><svg viewBox="0 0 16 16"><circle cx="8" cy="8" r="7"/><path d="M1 8h14M8 1c-3 4-3 10 0 14M8 1c3 4 3 10 0 14" stroke="#1d1b1f" stroke-width="1" fill="none"/></svg>www.rwofficepartners.com.au</li>
    </ul>
    <ul class="socials">
      <li><span class="social-mark"></span>@rwofficepartners</li>
      <li><span class="social-mark"></span>@rwofficepartners</li>
    </ul>
  </section>
</body>
</html>
```